1 Page for Computer Repair Website

Looking for a 1 page website with a design that compliments the business card and pamphlet that have already been made (attached files). It should look business professional and easy to read. Email and phone number should be somewhere near the top of the website, visible when the page loads. I don't want any forms for people to mess with. No "Contact Us" form or entering in email for newsletter. Customers will just be looking at this site to confirm we are professionals and have our business in order.

Target Market(s)

Home and small business

Industry/Entity Type

Computer Repair

Coding

Coded - Design and coding required

Number of Pages Required

1 page

Font styles to use
Other font styles liked:
• Helvetica variations used in pamphlet and card

Colors
0455a3
cfdeed
85abd2
3276b5
85cae6
ffffff

Requirements
Must have
• Compliment the pamphlet and business card in color choices and font use. Pleasing to the eye and easy to read through categories and text.
Should not have
• Forms. No "enter name and email here" or anything of the sort.

```html
<!DOCTYPE html>
<html lang="en">
<head>
<meta charset="utf-8">
<title>KeyByte Computer Services</title>
<link href="https://fonts.googleapis.com/css2?family=Roboto:wght@300;400;500&display=swap" rel="stylesheet">
<style>
:root{
  --navy:#0455a3;
  --blue:#3276b5;
  --mid:#85abd2;
  --pale:#cfdeed;
  --sky:#85cae6;
  --white:#ffffff;
  --ink:#333a44;
  --deep:#0b2f5e;
}
*{margin:0;padding:0;box-sizing:border-box}
html,body{width:679px;height:1200px;overflow:hidden}
body{font-family:"Roboto",Helvetica,Arial,sans-serif;color:var(--ink);background:var(--white);position:relative}
.site-header{height:62px;display:flex;align-items:center;justify-content:space-between;padding:0 20px 0 16px;background:var(--white)}
.brand{color:var(--navy);line-height:1}
.brand-name{font-size:30px;font-weight:300;letter-spacing:.5px}
.brand-tag{font-size:10px;font-weight:300;color:var(--mid);margin-top:2px}
.header-right{display:flex;flex-direction:column;align-items:flex-end;height:62px}
.header-contact{font-size:9px;color:var(--blue);padding-top:5px;height:16px;display:flex;gap:14px}
.main-nav{display:flex}
.main-nav a{color:var(--navy);text-decoration:none;font-size:13px;padding:0 22px;line-height:44px;display:block}
.main-nav a.active{border-bottom:2px solid var(--navy);line-height:44px;height:46px}
.hero{position:relative;height:298px}
.hero-photo{position:absolute;inset:0;background:linear-gradient(100deg,#6d7680 0%,#b9c0c8 40%,#dde1e4 70%,#c9cdd0 100%)}
.hero-copy{position:absolute;right:26px;top:90px;width:290px;text-align:right}
.hero-copy h1{font-size:19px;font-weight:300;color:#222;line-height:1.25}
.hero-copy p{font-size:14px;color:var(--navy);margin-top:6px;line-height:1.3}
.slider-dots{position:absolute;left:50%;transform:translateX(-50%);display:flex;gap:16px;align-items:center}
.dot{width:18px;height:18px;border-radius:50%;background:var(--white);display:flex;align-items:center;justify-content:center}
.dot::after{content:"";width:6px;height:6px;border-radius:50%;background:var(--mid)}
.dot.current{width:26px;height:26px}
.dot.current::after{width:12px;height:12px;background:var(--blue)}
.hero .slider-dots{bottom:-8px}
.section-title{text-align:center;color:var(--navy);font-size:23px;font-weight:400}
.section-title::after{content:"";display:block;width:70px;height:1px;background:var(--navy);margin:9px auto 0}
.about{padding-top:28px;height:205px;text-align:center}
.about p{width:480px;margin:20px auto 0;font-size:11px;line-height:1.6;color:#444}
.btn{display:inline-block;border:1px solid var(--navy);color:var(--navy);font-size:11px;padding:4px 18px;background:var(--white);text-decoration:none}
.about .btn{margin-top:18px}
.services{background:var(--pale);height:298px;padding-top:28px;text-align:center;position:relative}
.service-row{display:flex;justify-content:center;gap:30px;margin-top:22px}
.service{position:relative;width:160px;height:160px;border-radius:50%;background:var(--white);padding:34px 18px 0}
.service.featured{background:var(--blue);color:var(--white)}
.service h3{font-size:13px;font-weight:400;color:var(--navy)}
.service.featured h3{color:var(--white)}
.service p{font-size:8.5px;line-height:1.45;margin-top:8px}
.service .more{font-size:9px;text-decoration:underline;margin-top:6px;display:block;color:var(--navy)}
.service.featured .more{color:var(--white)}
.service-icon{position:absolute;right:-22px;bottom:-6px;width:62px;height:62px;border-radius:50%;background:var(--white);border:3px solid var(--white);display:flex;align-items:center;justify-content:center;box-shadow:0 0 0 1px var(--pale)}
.service.featured .service-icon{background:var(--navy)}
.services .btn{margin-top:28px;background:transparent}
.reasons{padding-top:34px;height:215px}
.testimonial{width:480px;margin:24px auto 0;border:1px solid var(--mid);padding:14px 22px 10px 28px;font-size:10.5px;line-height:1.6;position:relative}
.testimonial::before{content:"\201C";position:absolute;left:10px;top:6px;font-size:20px;color:var(--navy)}
.testimonial cite{display:block;text-align:right;font-style:normal;margin-top:14px;font-size:10px}
.site-footer{position:absolute;left:0;right:0;top:1078px;height:122px;background:linear-gradient(90deg,var(--blue),var(--navy));color:var(--white)}
.site-footer .slider-dots{top:-9px}
.footer-cols{display:flex;justify-content:space-between;padding:30px 70px 0 120px}
.footer-col h4{font-size:12px;font-weight:400;margin-bottom:10px}
.social{display:flex;gap:12px;margin-left:4px}
.social span{width:14px;height:14px;border-radius:50%;background:var(--sky)}
.contact-line{display:flex;align-items:center;gap:7px;font-size:10px;margin-bottom:6px}
.contact-line i{width:13px;height:13px;border-radius:50%;background:var(--white);display:flex;align-items:center;justify-content:center}
.legal{position:absolute;left:0;right:0;bottom:0;height:15px;background:var(--deep);color:var(--white);font-size:7px;text-align:center;line-height:15px}
</style>
</head>
<body>
<header class="site-header">
  <div class="brand">
    <div class="brand-name">KeyByte</div>
    <div class="brand-tag">Computer Services</div>
  </div>
  <div class="header-right">
    <div class="header-contact"><span>hello@keybyte.example</span><span>555 012 3487</span></div>
    <nav class="main-nav">
      <a href="#" class="active">HOME</a>
      <a href="#">ABOUT US</a>
      <a href="#">SERVICES</a>
      <a href="#">CONTACT US</a>
    </nav>
  </div>
</header>

<section class="hero">
  <div class="hero-photo" role="img" aria-label="Photo of a technician working at a computer in a bright office"></div>
  <div class="hero-copy">
    <h1>WE PROVIDE A BEST COMPUTER SERVICES</h1>
    <p>Lorem Ipsum is simply dummy text of the printing and typesetting industry.</p>
  </div>
  <div class="slider-dots"><span class="dot"></span><span class="dot current"></span><span class="dot"></span></div>
</section>

<section class="about">
  <h2 class="section-title">Know About Us</h2>
  <p>Lorem Ipsum is simply dummy text of the printing and typesetting industry. Lorem Ipsum has been the industry's standard dummy text ever since the 1500s, when an unknown printer took a galley of type and scrambled it to make a type specimen book. Lorem Ipsum is simply dummy text of the printing and typesetting industry.</p>
  <a class="btn" href="#">Read More</a>
</section>

<section class="services">
  <h2 class="section-title">Our Services</h2>
  <div class="service-row">
    <div class="service">
      <h3>Honest Service</h3>
      <p>Our certified technicians won't push on commission. No pressure to upgrade to products / services</p>
      <a class="more" href="#">Know More</a>
      <span class="service-icon"><svg width="32" height="32" viewBox="0 0 32 32"><g fill="none" stroke="#3276b5" stroke-width="3"><circle cx="12" cy="13" r="5"/><circle cx="23" cy="22" r="3.5"/></g><g stroke="#3276b5" stroke-width="3" stroke-linecap="round"><path d="M12 3v3M12 20v3M2 13h3M19 13h3M5 6l2 2M17 18l2 2M5 20l2-2M17 8l2-2"/></g></svg></span>
    </div>
    <div class="service featured">
      <h3>Malware/Virus Removal</h3>
      <p>Infections can come from many places and sometimes antivirus just isn't enough</p>
      <a class="more" href="#">Know More</a>
      <span class="service-icon"><svg width="30" height="30" viewBox="0 0 30 30"><path d="M15 3l10 4v7c0 7-5 11-10 13C10 25 5 21 5 14V7z" fill="#ffffff"/><path d="M10 15l4 4 6-8" fill="none" stroke="#0455a3" stroke-width="3" stroke-linecap="round"/></svg></span>
    </div>
    <div class="service">
      <h3>In-Home Installation</h3>
      <p>All our services come with pick-up and drop off installation. You won't be left to set up wireless</p>
      <a class="more" href="#">Know More</a>
      <span class="service-icon"><svg width="30" height="30" viewBox="0 0 30 30"><g stroke="#3276b5" stroke-width="4" stroke-linecap="round"><path d="M7 23L21 9"/><path d="M8 8l15 15"/></g><circle cx="22" cy="8" r="4" fill="#3276b5"/></svg></span>
    </div>
  </div>
  <a class="btn" href="#">View All</a>
</section>

<section class="reasons">
  <h2 class="section-title">Why People Choose Us</h2>
  <blockquote class="testimonial">
    Lorem Ipsum is simply dummy text of the printing and typesetting industry. Lorem Ipsum has been the industry's standard dummy text ever. Lorem Ipsum is simply dummy text of the printing and typesetting industry.
    <cite>Marla</cite>
  </blockquote>
</section>

<footer class="site-footer">
  <div class="slider-dots"><span class="dot"></span><span class="dot"></span><span class="dot current"></span><span class="dot"></span><span class="dot"></span></div>
  <div class="footer-cols">
    <div class="footer-col">
      <h4>Follow Us On</h4>
      <div class="social"><span></span><span></span><span></span><span></span></div>
    </div>
    <div class="footer-col">
      <h4>Can Call us when you need Us</h4>
      <div class="contact-line"><i><svg width="9" height="7" viewBox="0 0 9 7"><rect x=".5" y=".5" width="8" height="6" fill="none" stroke="#0455a3"/><path d="M.5 .5l4 3 4-3" fill="none" stroke="#0455a3"/></svg></i>hello@keybyte.example</div>
      <div class="contact-line"><i><svg width="8" height="8" viewBox="0 0 8 8"><path d="M1 1h2l1 2-1 1c.5 1 1 1.5 2 2l1-1 2 1v2C4 8 0 4 1 1z" fill="#0455a3"/></svg></i>555 012 3487</div>
    </div>
  </div>
  <div class="legal">© 2015, All Rights Reserved.</div>
</footer>
</body>
</html>
```